Website for new dental office

I am Dr. Colin Ashford and am building a new dental practice. I specialize in general dentistry. I am young and have a higher end dental practice incorporating very new technologies and would like my website to reflect that. As many dental patients are older, the website must be very easy to navigate. I would like patients to be able to request appointments, and will eventually add on patient information forms (the health history, etc, that you normally fill out in the practice) from my practice management software, so leave an area for that.

Industry/Entity Type

Building

```html
<!DOCTYPE html>
<html lang="en">
<head>
<meta charset="utf-8">
<title>Ashford Dental</title>
<link href="https://fonts.googleapis.com/css2?family=Open+Sans:ital,wght@0,400;0,600;0,700;1,400&display=swap" rel="stylesheet">
<style>
:root{
  --sky-top:#cfe6f7;
  --sky-mid:#eef6fc;
  --white:#ffffff;
  --brand:#139fe0;
  --brand-deep:#1a5aa6;
  --nav-top:#2db6ee;
  --nav-bottom:#0b93dc;
  --nav-divider:#0a7fc0;
  --text:#555b60;
  --text-soft:#6b7176;
  --heading:#474c50;
  --field-line:#cfd3d6;
  --field-bg:#f7f8f9;
  --submit-top:#1f6fcb;
  --submit-bottom:#0d4a9c;
  --panel-line:#d6dadd;
  --footer-bg:#f3f4f5;
}
*{box-sizing:border-box;margin:0;padding:0}
html,body{width:1200px;height:1144px;overflow:hidden}
body{
  position:relative;
  font-family:"Open Sans",sans-serif;
  color:var(--text);
  background:linear-gradient(180deg,var(--sky-top) 0,var(--sky-mid) 420px,var(--white) 640px);
}
.abs{position:absolute}

/* header */
.brand{left:186px;top:58px;font-size:31px;font-weight:600;color:var(--brand);letter-spacing:.2px;display:flex;align-items:center;gap:10px}
.brand-dot{width:14px;height:14px;border-radius:50%;background:var(--brand)}
.contact{right:184px;top:50px;text-align:right}
.contact-label{font-size:14px;color:var(--brand);line-height:18px}
.contact-phone{font-size:24px;color:var(--brand-deep);line-height:30px}

/* nav */
.main-nav{left:180px;top:111px;width:841px;height:45px;display:flex;border-radius:4px 4px 0 0;
  background:linear-gradient(180deg,var(--nav-top),var(--nav-bottom));}
.main-nav a{color:var(--white);text-decoration:none;font-size:14px;display:flex;align-items:center;justify-content:center;border-right:1px solid var(--nav-divider)}
.main-nav a:last-child{border-right:0}

/* hero */
.hero{left:180px;top:156px;width:841px;height:347px;background:var(--white);border:1px solid #dfe3e6;border-top:0;border-radius:0 0 4px 4px;overflow:hidden}
.hero-photo{position:absolute;left:300px;top:0;right:0;bottom:0;
  background:linear-gradient(90deg,rgba(255,255,255,1) 0,rgba(214,232,246,.8) 18%,#bcd9ef 45%,#a9cbe6 75%,#c7deef 100%)}
.hero-title{position:absolute;left:47px;top:104px;font-size:36px;font-weight:700;color:var(--brand);line-height:42px;letter-spacing:.3px}
.hero-sub{position:absolute;left:47px;top:147px;font-size:20px;font-weight:600;color:var(--brand-deep);line-height:26px}
.hero-text{position:absolute;left:47px;top:177px;width:310px;font-size:11px;line-height:17px;color:var(--text-soft)}
.hero-dots{position:absolute;left:47px;top:221px;display:flex;gap:4px}
.hero-dots span{width:10px;height:10px;border-radius:50%;background:#b8bcc0}
.hero-dots span:first-child{background:var(--brand-deep)}

/* welcome */
.welcome-title{left:184px;top:543px;font-size:24px;color:var(--heading);font-weight:400}
.welcome-title em{font-style:normal;color:var(--brand-deep)}
.welcome-lead{left:185px;top:582px;width:570px;font-size:12.5px;line-height:20px;color:var(--text-soft)}
.welcome-body{left:185px;top:629px;width:570px;font-size:10.5px;line-height:19.7px;color:var(--text)}

/* feature columns */
.feature{top:744px;width:180px}
.feature h3{font-size:19px;font-weight:400;color:var(--brand);line-height:24px;margin-bottom:7px}
.feature-photo{width:175px;height:90px}
.feature h4{font-size:11.5px;font-weight:600;color:var(--heading);margin-top:9px;line-height:16px}
.feature p{font-size:9.5px;line-height:16.4px;color:var(--text-soft);margin-top:2px;width:170px;text-align:justify}
.btn{display:inline-block;margin-top:12px;width:88px;height:25px;line-height:25px;text-align:center;font-size:10.5px;font-weight:600;color:var(--white);border-radius:3px;
  background:linear-gradient(180deg,var(--nav-top),var(--nav-bottom))}

/* appointment form */
.appt{left:784px;top:539px;width:234px;height:273px;background:var(--white);border:1px solid var(--panel-line);border-radius:3px;overflow:hidden}
.appt h2{height:44px;line-height:44px;padding-left:17px;font-size:18px;font-weight:400;color:var(--white);
  background:linear-gradient(180deg,var(--nav-top),var(--nav-bottom))}
.field{position:absolute;left:19px;width:196px;height:25px;border:1px solid var(--field-line);background:var(--field-bg);font-size:9.5px;color:var(--text-soft);line-height:23px;padding-left:10px}
.submit{position:absolute;left:17px;top:219px;width:197px;height:31px;line-height:31px;text-align:center;color:var(--white);font-size:12px;font-weight:600;border-radius:3px;
  background:linear-gradient(180deg,var(--submit-top),var(--submit-bottom))}

/* testimonial */
.quote{left:782px;top:822px;width:238px;height:155px;border:1px solid var(--panel-line);border-radius:3px;background:linear-gradient(180deg,#ffffff,#eceeef)}
.quote-mark{position:absolute;left:11px;top:12px}
.quote p{position:absolute;left:31px;top:17px;width:195px;font-style:italic;font-size:10.5px;line-height:18px;color:var(--text)}
.quote-author{position:absolute;left:31px;top:126px;font-size:10.5px;color:var(--heading)}
.quote-nav{position:absolute;right:14px;top:124px}

/* footer */
.footer{left:0;top:1033px;width:1200px;height:111px;background:linear-gradient(180deg,#e9ebed 0,var(--footer-bg) 12px,var(--white) 100%)}
.footer-links{position:absolute;left:183px;top:31px;font-size:12.5px;color:var(--heading)}
.footer-links span{color:var(--heading);margin:0 6px}
.footer-copy{position:absolute;left:183px;top:57px;font-size:9.5px;color:var(--text-soft)}
.social{position:absolute;left:941px;top:27px;display:flex;gap:8px}
.social span{width:19px;height:19px;border-radius:2px}
</style>
</head>
<body>

<header>
  <div class="abs brand"><span class="brand-dot"></span>Ashford Dental</div>
  <div class="abs contact">
    <div class="contact-label">Make Appointment</div>
    <div class="contact-phone">555-014-2290</div>
  </div>
</header>

<nav class="abs main-nav">
  <a style="width:87px">Home</a>
  <a style="width:96px">About Us</a>
  <a style="width:150px">Treatment &amp; Care</a>
  <a style="width:88px">Services</a>
  <a style="width:134px">Success Stories</a>
  <a style="width:93px">Practices</a>
  <a style="width:88px">Support</a>
  <a style="width:105px">Contact</a>
</nav>

<section class="abs hero">
  <div class="hero-photo" role="img" aria-label="Smiling dentist treating a smiling female patient in the dental chair"></div>
  <h1 class="hero-title">DENTAL TREATMENT</h1>
  <div class="hero-sub">AND HIGHER END DENTAL PRACTICE</div>
  <p class="hero-text">Pellentesque habitant morbi tristique senectus et netus et malesuada fames ac turpis egestas.</p>
  <div class="hero-dots"><span></span><span></span><span></span><span></span></div>
</section>

<h2 class="abs welcome-title">Welcome to <em>Ashford Dental Clinic</em></h2>
<p class="abs welcome-lead">Donec iaculis diam a nisi accumsan viverra Duis sed tellus et tortor vestibulum gravida Praesent elementum elit at tellus Curabitur metus ipsum luctus eu</p>
<p class="abs welcome-body">Curabitur iaculis tempus eros Curabitur vel mi sit amet magna malesuada ultrices Ut nisi erat fermentum vel congue id euismod in elit Fusce ultricies orci ac feugiat suscipit leo massa sodales velit et scelerisque mi tortor at ipsum Proin orci odio commodo ac gravida non tristique vel tellus Pellentesque nibh libero ultricies eu sagittis non mollis sed justo Praesent metus ipsum pulvinar pulvinar porta id fringilla at est Phasellus felis dolor scelerisque</p>

<article class="abs feature" style="left:183px">
  <h3>Dental Practice</h3>
  <div class="feature-photo" role="img" aria-label="Dentist examining a young patient" style="background:linear-gradient(90deg,#bfe4ef,#e9f4f6 55%,#e8c9b3)"></div>
  <h4>Class aptent taciti</h4>
  <p>Donec scelerisque leo ac risus Praesent sit amet est In dictum dolo r eu dictum porttitor enim</p>
  <span class="btn">READ MORE</span>
</article>

<article class="abs feature" style="left:374px">
  <h3>Services Provide</h3>
  <div class="feature-photo" role="img" aria-label="Masked dentists performing a treatment" style="background:linear-gradient(90deg,#9aa3ab,#dfe3e6 50%,#8e969c)"></div>
  <h4>Class aptent taciti</h4>
  <p>Donec scelerisque leo ac risus Praesent sit amet est In dictum dolo r eu dictum porttitor enim</p>
  <span class="btn">READ MORE</span>
</article>

<article class="abs feature" style="left:565px">
  <h3>Our Technology</h3>
  <div class="feature-photo" role="img" aria-label="Modern treatment room with dental chair" style="background:linear-gradient(90deg,#e6eaec,#f4f6f7 50%,#5fb8a8)"></div>
  <h4>Class aptent taciti</h4>
  <p>Donec scelerisque leo ac risus Praesent sit amet est In dictum dolo r eu dictum porttitor enim</p>
  <span class="btn">READ MORE</span>
</article>

<aside class="abs appt">
  <h2>Request Appointment</h2>
  <div class="field" style="top:57px">Your name</div>
  <div class="field" style="top:89px">Phone no.</div>
  <div class="field" style="top:120px">Email address</div>
  <div class="field" style="top:152px;width:95px">Select Date</div>
  <div class="field" style="top:152px;left:118px;width:97px">Select Time</div>
  <div class="field" style="top:185px">Purpose to meet</div>
  <div class="submit">SUBMIT NOW</div>
</aside>

<aside class="abs quote">
  <svg class="quote-mark" width="18" height="13" viewBox="0 0 18 13" aria-hidden="true">
    <path d="M0 13V8C0 3 2 .5 6.5 0v2.5C4.5 3 3.5 4.5 3.5 6.5H7V13zM10 13V8c0-5 2-7.5 6.5-8v2.5c-2 .5-3 2-3 4H17V13z" fill="#6b7176"/>
  </svg>
  <p>Proin orci odio commodo ac gravida non tristique vel tellus Pellentesque nibh libero ultricies eu sagittis non mollis sed justo Praesent metus ipsum pulvinar pulvinar porta id frin
    <svg width="14" height="10" viewBox="0 0 18 13" aria-hidden="true" style="vertical-align:-1px;margin-left:4px"><path d="M17 0v5c0 5-2 7.5-6.5 8v-2.5c2-.5 3-2 3-4H10V0zM7 0v5c0 5-2 7.5-6.5 8v-2.5c2-.5 3-2 3-4H0V0z" fill="#6b7176"/></svg>
  </p>
  <div class="quote-author">By Author Name</div>
  <svg class="quote-nav" width="22" height="14" viewBox="0 0 22 14" aria-hidden="true">
    <path d="M7 1 1 7l6 6M15 1l6 6-6 6" fill="none" stroke="#6b7176" stroke-width="1.4"/>
  </svg>
</aside>

<footer class="abs footer">
  <div class="footer-links">Home<span>|</span>About Us<span>|</span>Treatment &amp; Care<span>|</span>Services<span>|</span>Success Stories<span>|</span>Practices<span>|</span>Support<span>|</span>Contact</div>
  <div class="footer-copy">© 2014 Company Name.&nbsp; All right reserved.&nbsp; Term of Use</div>
  <div class="social" aria-label="Social links">
    <span style="background:#3b5a98"></span>
    <span style="background:#3fb0e6"></span>
    <span style="background:#1477b6"></span>
  </div>
</footer>

</body>
</html>
```